KVOR Individual and Corporate Development Business Card Design

KVOR needs a business card design that is aligned with it's values and targetted markets. Coherent Lattice of Adaptive Reasoning Method's self diagnosis model and tools, which can be used for personal improvement and team/business performance enhancement, is based on the learnings of over 20 years of medical practitioning. KVOR supercharges personal effectiveness and awareness to also increase team and business performance.

The targetted markets are high performance individuals and teams who aspire seek to enhance their capabilities and achieve their absolute best potential.

Look and feel for the business card design we are looking for is high technology, premium, fresh, new and medical.

Target Market(s)

Industry/Entity Type

Business Consultant

Contact Information for Business Card

Logo, Full Name, Title, Phone number, Email, company name, Address,

Font styles to use
Sans Serif

Requirements
Must have
• Tag line: Elevating Focus for Purposefully Driven Leaders
• Please use same colours as the logo.

```html
<!DOCTYPE html>
<html lang="en">
<head>
<meta charset="utf-8">
<title>KVOR Business Card</title>
<link href="https://fonts.googleapis.com/css2?family=Montserrat:wght@600;700&family=Roboto:wght@400;500&display=swap" rel="stylesheet">
<style>
  :root {
    --teal: #0aa7c0;
    --teal-line: #6cc7d6;
    --grey: #636468;
    --text-grey: #555a60;
    --rule-grey: #c9cbce;
    --card: #ffffff;
    --backdrop: #2e2f31;
  }
  * { margin: 0; padding: 0; box-sizing: border-box; }
  html, body { width: 1200px; height: 880px; overflow: hidden; }
  body {
    background: var(--backdrop);
    position: relative;
    font-family: "Roboto", Arial, sans-serif;
  }
  .card {
    position: absolute;
    width: 560px;
    height: 320px;
    background: var(--card);
    border-radius: 16px;
    overflow: hidden;
    box-shadow: 0 18px 40px rgba(0,0,0,0.45);
  }
  .card--front { left: 70px; top: 70px; }
  .card--back { left: 570px; top: 490px; }

  .brand { position: absolute; text-align: left; }
  .brand__mark { display: flex; align-items: center; gap: 12px; }
  .brand__dot {
    width: 26px; height: 26px; border-radius: 50%;
    background: var(--teal);
  }
  .brand__name {
    font-family: "Montserrat", Arial, sans-serif;
    font-weight: 700;
    color: var(--teal);
    letter-spacing: 3px;
    line-height: 1;
  }
  .brand__rule { height: 2px; background: var(--rule-grey); margin: 8px 0 6px; }
  .brand__full {
    font-family: "Montserrat", Arial, sans-serif;
    font-weight: 600;
    color: var(--teal);
    text-transform: uppercase;
    line-height: 1.2;
  }

  .card--front .brand { left: 50%; top: 92px; transform: translateX(-50%); width: 300px; }
  .card--front .brand__name { font-size: 64px; }
  .card--front .brand__full { font-size: 12px; }
  .tagline {
    position: absolute; left: 0; right: 0; top: 232px;
    text-align: center;
    color: var(--teal);
    font-size: 16px;
    letter-spacing: 1px;
  }

  .card--back .brand { right: 34px; top: 34px; width: 250px; }
  .card--back .brand__name { font-size: 52px; }
  .card--back .brand__full { font-size: 10px; }

  .person { position: absolute; left: 34px; right: 34px; top: 178px; }
  .person__row { display: flex; align-items: flex-end; }
  .person__name {
    font-family: "Montserrat", Arial, sans-serif;
    font-weight: 600; font-size: 19px; color: var(--teal); letter-spacing: 0.5px;
    line-height: 1.1; white-space: nowrap;
  }
  .person__rule {
    flex: 1; height: 1px; background: var(--teal-line);
    margin: 0 0 5px 12px;
  }
  .person__title { font-size: 14px; color: var(--text-grey); margin-top: 2px; }

  .contact { position: absolute; left: 34px; top: 232px; list-style: none; }
  .contact__item {
    display: flex; align-items: center; gap: 7px;
    font-size: 14px; color: var(--text-grey); margin-bottom: 5px;
  }
  .contact__icon { width: 18px; height: 18px; }

  .address {
    position: absolute; right: 34px; top: 210px;
    text-align: right; font-size: 13px; line-height: 1.35; color: var(--text-grey);
  }
  .band-grey {
    position: absolute; left: 0; bottom: 0; width: 400px; height: 16px;
    background: var(--grey);
  }
  .band-teal {
    position: absolute; right: 0; bottom: 0; width: 160px; height: 62px;
    background: var(--teal);
  }
</style>
</head>
<body>
  <section class="card card--front">
    <div class="brand">
      <div class="brand__mark">
        <span class="brand__dot"></span>
        <span class="brand__name">KVOR</span>
      </div>
      <div class="brand__rule"></div>
      <p class="brand__full">Coherent Lattice of<br>Adaptive Reasoning Method</p>
    </div>
    <p class="tagline">Elevating Focus for Purposefully Driven Leaders</p>
  </section>

  <section class="card card--back">
    <div class="brand">
      <div class="brand__mark">
        <span class="brand__dot"></span>
        <span class="brand__name">KVOR</span>
      </div>
      <div class="brand__rule"></div>
      <p class="brand__full">Coherent Lattice of<br>Adaptive Reasoning Method</p>
    </div>

    <div class="person">
      <div class="person__row">
        <p class="person__name">DANIEL OKAFOR</p>
        <span class="person__rule"></span>
      </div>
      <p class="person__title">Founder</p>
    </div>

    <ul class="contact">
      <li class="contact__item">
        <svg class="contact__icon" viewBox="0 0 18 18" aria-hidden="true">
          <circle cx="9" cy="9" r="8" fill="none" stroke="#0aa7c0" stroke-width="1.4"/>
          <rect x="6.2" y="4.2" width="5.6" height="9.6" rx="1" fill="none" stroke="#0aa7c0" stroke-width="1.2"/>
        </svg>
        (555) 318-2046
      </li>
      <li class="contact__item">
        <svg class="contact__icon" viewBox="0 0 18 18" aria-hidden="true">
          <circle cx="9" cy="9" r="8" fill="none" stroke="#0aa7c0" stroke-width="1.4"/>
          <rect x="4.5" y="6" width="9" height="6" fill="none" stroke="#0aa7c0" stroke-width="1.2"/>
          <path d="M4.5 6 L9 9.5 L13.5 6" fill="none" stroke="#0aa7c0" stroke-width="1.2"/>
        </svg>
        hello@kvormethod.com
      </li>
    </ul>

    <p class="address">PO Box 418 Lantern Lane<br>7th Avenue Harlow Bay</p>

    <div class="band-grey"></div>
    <div class="band-teal"></div>
  </section>
</body>
</html>
```